Detail Shop Business card design

i need a business card design for my new detailing company called 'Brisk's Polish Works'. i want an all black and white design . simple, direct and to the point. i want the designer to choose a fitting font to match the logothe front should have logo, address, phone and email and the back side should have a slogan and text indicating that we offer services on anything including cars, trucks, motorcycles and RVs. slogan will read "we take pride in your ride"
maybe also very small on the back side the IG icon with Brisks_Polish_Works

phone 208.417.6352
address 3847 E Larkin Ave
Spokane WA 99214
email: BrisksPolish@mailvexo.com

Target Market(s)

all ages , auto enthusiasts

Industry/Entity Type

Automotive

Contact Information for Business Card

the front should have logo, address, phone and email and the back side should have a slogan and text indicating that we offer services on anything including cars, trucks, motorcycles and RVs. slogan will read "we take pride in your ride"

phone 208.417.6352
address 3847 E Larkin Ave
Spokane WA 99214

Colors
000000
ffffff

Requirements
Must have
• bold font and very simple design with good spacing
Nice to have
• anything creative from the designer indicating we service any types of vehicles
Should not have
• any colors ,

```html
<!DOCTYPE html>
<html lang="en">
<head>
<meta charset="utf-8">
<title>Brisk's Polish Works – Business Card</title>
<link href="https://fonts.googleapis.com/css2?family=Arimo:wght@400;700&family=Oswald:wght@400;600&display=swap" rel="stylesheet">
<style>
  :root {
    --ink: #000000;
    --paper: #ffffff;
    --muted: #444444;
    --backdrop: #e6e6e6;
  }
  * { margin: 0; padding: 0; box-sizing: border-box; }
  html, body { width: 1200px; height: 886px; overflow: hidden; }
  body {
    background: var(--backdrop);
    display: flex;
    align-items: center;
    justify-content: center;
    gap: 60px;
    font-family: "Arimo", Arial, sans-serif;
    color: var(--ink);
  }
  .card {
    width: 400px;
    height: 700px;
    background: var(--paper);
    position: relative;
    box-shadow: 0 6px 20px rgba(0,0,0,0.18);
  }

  /* Front */
  .brand-mark {
    position: absolute;
    top: 120px;
    left: 0; right: 0;
    display: flex;
    flex-direction: column;
    align-items: center;
    gap: 14px;
  }
  .brand-mark .dot {
    width: 22px; height: 22px;
    border-radius: 50%;
    background: var(--ink);
  }
  .brand-name {
    font-weight: 700;
    font-size: 30px;
    letter-spacing: 1px;
    text-transform: uppercase;
    text-align: center;
    line-height: 1.15;
  }
  .front-rule {
    position: absolute;
    top: 412px;
    left: 100px;
    width: 200px;
    height: 4px;
    background: var(--ink);
  }
  .contact {
    position: absolute;
    top: 440px;
    left: 70px;
    right: 40px;
    font-size: 15px;
    line-height: 1.55;
    color: var(--muted);
  }
  .contact .person {
    font-weight: 700;
    font-size: 20px;
    color: var(--ink);
    letter-spacing: 0.5px;
    margin-left: 48px;
  }
  .contact .role {
    margin-left: 48px;
    letter-spacing: 0.5px;
    margin-bottom: 6px;
  }
  .contact b { color: var(--ink); }

  /* Back */
  .vehicle-art {
    position: absolute;
    top: 440px;
    left: 40px;
    width: 320px;
    height: 90px;
  }
  .ground-rule {
    position: absolute;
    top: 540px;
    left: 30px;
    width: 340px;
    height: 2px;
    background: var(--ink);
  }
  .slogan {
    position: absolute;
    top: 548px;
    left: 0; right: 0;
    text-align: center;
    font-family: "Oswald", "Arial Narrow", sans-serif;
    font-weight: 600;
    font-size: 22px;
    letter-spacing: 1px;
    text-transform: uppercase;
  }
  .services {
    position: absolute;
    top: 584px;
    left: 40px; right: 40px;
    text-align: center;
    font-family: "Oswald", "Arial Narrow", sans-serif;
    font-weight: 400;
    font-size: 15px;
    line-height: 1.3;
  }
  .base-rule {
    position: absolute;
    top: 632px;
    left: 30px;
    width: 340px;
    height: 1px;
    background: var(--ink);
  }
</style>
</head>
<body>
  <section class="card card-front">
    <div class="brand-mark">
      <span class="dot"></span>
      <div class="brand-name">Brisk's<br>Polish Works</div>
    </div>
    <div class="front-rule"></div>
    <div class="contact">
      <div class="person">DALE MERCER</div>
      <div class="role">CEO/FOUNDER</div>
      <div>3847 E Larkin Ave Spokane WA 99214</div>
      <div><b>P:</b> 208.417.6352 <b>M:</b> 208 593 7140</div>
      <div><b>E:</b> BrisksPolish@mailvexo.com</div>
      <div><b>W:</b> www.briskspolish.com</div>
    </div>
  </section>

  <section class="card card-back">
    <svg class="vehicle-art" viewBox="0 0 320 90" role="img" aria-label="Black silhouette illustration of a classic hot rod car">
      <defs>
        <linearGradient id="artTone" x1="0" y1="0" x2="1" y2="0">
          <stop offset="0" stop-color="#1a1a1a"/>
          <stop offset="1" stop-color="#3a3a3a"/>
        </linearGradient>
      </defs>
      <rect x="0" y="0" width="320" height="90" fill="url(#artTone)"/>
    </svg>
    <div class="ground-rule"></div>
    <div class="slogan">We take pride in your ride</div>
    <div class="services">we offer services on anything including cars,<br>trucks, motorcycles &amp; RVs</div>
    <div class="base-rule"></div>
  </section>
</body>
</html>
```